Industrial Company-Pop-Up Banner Design for Demolition and Infrastructure Company

Hi-
We need to create 2 pop-up banners for our company. They will both have the same logo, but different photos. We would like to have the colors white, red, and black and feature a modern design. I have attached some inspiration photos.

Target Market(s)

Trade Show/Job Fair Audience

Industry/Entity Type

construction, industrial

Font styles to use
Sans Serif

Colors
EB3D1F
EC4F4E
F09395
F8D3D4
FCEDEE

Requirements
Must have
• 2 versions, each with different photos but same design. Logo, Red, Black, and White Color Scheme, Modern Design
Nice to have
• Modern Design similar to the inspiration photos

```html
<!DOCTYPE html>
<html lang="en">
<head>
<meta charset="utf-8">
<title>Ironvale – Pop-Up Banners</title>
<link rel="stylesheet" href="https://fonts.googleapis.com/css2?family=Poppins:wght@400;600;700;800;900&display=swap">
<style>
  :root {
    --red: #d71920;
    --black: #1c1c1c;
    --white: #ffffff;
    --page: #ffffff;
    --sky: #7fa9d6;
    --sky-light: #c9d9e6;
    --dirt: #c98a5c;
    --dirt-dark: #9c5a35;
    --foliage: #4e7a36;
    --steel: #a7a7a2;
    --steel-dark: #6e6e6a;
    --brick: #c2412a;
    --machine: #e6b422;
    --teal: #3f8aa3;
  }
  html, body {
    margin: 0;
    padding: 0;
    width: 760px;
    height: 1200px;
    overflow: hidden;
    background: var(--page);
    font-family: "Poppins", sans-serif;
  }
  .canvas {
    position: relative;
    width: 760px;
    height: 1200px;
  }
  .banner {
    position: absolute;
    top: 192px;
    width: 340px;
    height: 815px;
    box-shadow: 0 6px 14px rgba(0,0,0,0.28);
  }
  .banner--one { left: 25px; }
  .banner--two { left: 395px; }

  .fill-white { fill: var(--white); }
  .fill-black { fill: var(--black); }
  .fill-red { fill: var(--red); }

  .stop-sky { stop-color: var(--sky); }
  .stop-sky-light { stop-color: var(--sky-light); }
  .stop-dirt { stop-color: var(--dirt); }
  .stop-dirt-dark { stop-color: var(--dirt-dark); }
  .stop-foliage { stop-color: var(--foliage); }
  .stop-steel { stop-color: var(--steel); }
  .stop-steel-dark { stop-color: var(--steel-dark); }
  .stop-brick { stop-color: var(--brick); }
  .stop-machine { stop-color: var(--machine); }
  .stop-teal { stop-color: var(--teal); }

  .brand-name {
    font-family: "Poppins", sans-serif;
    font-weight: 800;
    font-size: 44px;
    letter-spacing: 1px;
    fill: var(--red);
  }
  .headline-shaping,
  .headline-skyline { fill: var(--red); font-family: "Poppins", sans-serif; }
  .headline-america { fill: var(--black); font-family: "Poppins", sans-serif; }
  .headline-shaping,
  .headline-america { font-weight: 800; font-size: 56px; }
  .headline-skyline { font-weight: 900; font-size: 104px; letter-spacing: -3px; }
  .since-text {
    fill: var(--white);
    font-size: 26px;
    letter-spacing: 9px;
    font-weight: 400;
  }
  .since-year { font-weight: 800; }
  .web-address {
    fill: var(--white);
    font-size: 27px;
    font-weight: 600;
    letter-spacing: 6px;
  }
  .web-accent { fill: var(--red); }
</style>
</head>
<body>
<main class="canvas">

  <!-- Banner version one -->
  <svg class="banner banner--one" viewBox="0 0 470 1127" xmlns="http://www.w3.org/2000/svg">
    <defs>
      <linearGradient id="b1-site-left" x1="0" y1="0" x2="0" y2="1">
        <stop offset="0" class="stop-sky-light"/>
        <stop offset="0.45" class="stop-steel"/>
        <stop offset="0.7" class="stop-brick"/>
        <stop offset="1" class="stop-steel-dark"/>
      </linearGradient>
      <linearGradient id="b1-site-top" x1="0" y1="0" x2="0" y2="1">
        <stop offset="0" class="stop-sky"/>
        <stop offset="0.45" class="stop-foliage"/>
        <stop offset="0.65" class="stop-dirt"/>
        <stop offset="1" class="stop-dirt-dark"/>
      </linearGradient>
      <linearGradient id="b1-site-mid" x1="0" y1="0" x2="0" y2="1">
        <stop offset="0" class="stop-sky"/>
        <stop offset="0.35" class="stop-foliage"/>
        <stop offset="0.6" class="stop-machine"/>
        <stop offset="1" class="stop-dirt"/>
      </linearGradient>
      <linearGradient id="b1-site-low" x1="0" y1="0" x2="0" y2="1">
        <stop offset="0" class="stop-sky-light"/>
        <stop offset="0.6" class="stop-steel"/>
        <stop offset="1" class="stop-foliage"/>
      </linearGradient>
    </defs>

    <rect class="fill-white" width="470" height="1127"/>

    <g role="img" aria-label="Excavator tearing down a brick industrial building">
      <polygon points="0,162 178,314 312,466 0,778" fill="url(#b1-site-left)"/>
    </g>
    <g role="img" aria-label="Articulated dump trucks and excavators working on a cleared dirt site">
      <polygon points="470,38 198,312 326,456 470,602" fill="url(#b1-site-top)"/>
    </g>
    <g role="img" aria-label="Excavator loading a yellow haul truck on red earth">
      <polygon points="322,472 462,614 332,746 190,616" fill="url(#b1-site-mid)"/>
    </g>
    <g role="img" aria-label="Demolition of an industrial plant structure">
      <polygon points="470,626 344,754 470,880" fill="url(#b1-site-low)"/>
    </g>

    <polygon class="fill-black" points="0,0 470,0 470,18 186,302 0,142"/>
    <polygon class="fill-red" points="226,676 250,652 448,852 424,876"/>

    <rect x="62" y="100" width="24" height="24" class="fill-red"/>
    <text class="brand-name" x="98" y="125">IRONVALE</text>

    <text class="headline-shaping" x="30" y="832">SHAPING</text>
    <text class="headline-america" x="30" y="886">AMERICA’S</text>
    <text class="headline-skyline" x="26" y="978" textLength="398" lengthAdjust="spacingAndGlyphs">SKYLINE</text>

    <polygon class="fill-black" points="52,986 380,986 358,1022 30,1022"/>
    <text class="since-text" x="200" y="1014" text-anchor="middle">SINCE <tspan class="since-year">1959</tspan></text>

    <rect class="fill-black" x="0" y="1055" width="470" height="72"/>
    <text class="web-address" x="235" y="1101" text-anchor="middle">www.<tspan class="web-accent">ironvale</tspan>.com</text>
  </svg>

  <!-- Banner version two -->
  <svg class="banner banner--two" viewBox="0 0 470 1127" xmlns="http://www.w3.org/2000/svg">
    <defs>
      <linearGradient id="b2-site-left" x1="0" y1="0" x2="0" y2="1">
        <stop offset="0" class="stop-sky-light"/>
        <stop offset="0.5" class="stop-steel"/>
        <stop offset="0.8" class="stop-steel-dark"/>
        <stop offset="1" class="stop-foliage"/>
      </linearGradient>
      <linearGradient id="b2-site-top" x1="0" y1="0" x2="0" y2="1">
        <stop offset="0" class="stop-sky"/>
        <stop offset="0.4" class="stop-steel"/>
        <stop offset="0.8" class="stop-steel-dark"/>
        <stop offset="1" class="stop-foliage"/>
      </linearGradient>
      <linearGradient id="b2-site-mid" x1="0" y1="0" x2="0" y2="1">
        <stop offset="0" class="stop-sky"/>
        <stop offset="0.35" class="stop-foliage"/>
        <stop offset="0.55" class="stop-machine"/>
        <stop offset="1" class="stop-dirt-dark"/>
      </linearGradient>
      <linearGradient id="b2-site-low" x1="0" y1="0" x2="0" y2="1">
        <stop offset="0" class="stop-sky-light"/>
        <stop offset="0.5" class="stop-teal"/>
        <stop offset="1" class="stop-steel"/>
      </linearGradient>
    </defs>

    <rect class="fill-white" width="470" height="1127"/>

    <g role="img" aria-label="Two red and white power plant smokestacks before demolition">
      <polygon points="0,162 178,314 312,466 0,778" fill="url(#b2-site-left)"/>
    </g>
    <g role="img" aria-label="Industrial plant tower with excavator clearing debris">
      <polygon points="470,38 198,312 326,456 470,602" fill="url(#b2-site-top)"/>
    </g>
    <g role="img" aria-label="Yellow haul truck crossing a red dirt site">
      <polygon points="322,472 462,614 332,746 190,616" fill="url(#b2-site-mid)"/>
    </g>
    <g role="img" aria-label="Blue industrial conveyor equipment over open fields">
      <polygon points="470,626 344,754 470,880" fill="url(#b2-site-low)"/>
    </g>

    <polygon class="fill-black" points="0,0 470,0 470,18 186,302 0,142"/>
    <polygon class="fill-red" points="226,676 250,652 448,852 424,876"/>

    <rect x="62" y="100" width="24" height="24" class="fill-red"/>
    <text class="brand-name" x="98" y="125">IRONVALE</text>

    <text class="headline-shaping" x="30" y="832">SHAPING</text>
    <text class="headline-america" x="30" y="886">AMERICA’S</text>
    <text class="headline-skyline" x="26" y="978" textLength="398" lengthAdjust="spacingAndGlyphs">SKYLINE</text>

    <polygon class="fill-black" points="52,986 380,986 358,1022 30,1022"/>
    <text class="since-text" x="200" y="1014" text-anchor="middle">SINCE <tspan class="since-year">1959</tspan></text>

    <rect class="fill-black" x="0" y="1055" width="470" height="72"/>
    <text class="web-address" x="235" y="1101" text-anchor="middle">www.<tspan class="web-accent">ironvale</tspan>.com</text>
  </svg>

</main>
</body>
</html>
```